Brightarc Orthodontics appointment card design

I need appointment cards/ business cards made. Front will be Logo, name, title, email, phone number and location (5263 Walnut Hollow Pkwy, Ste 412, Concord, NC 28027) . the back should have an appointment card (name, time, date) and also 3 addresses listed with a check box so we can check to which location they are going.
Dale Fenwick Orthodontics
- 6735 Orchard Street, Ste 514, Harrisburg, NC 28075
- 3647 Ridgeway Drive NE, Ste 810, Concord, NC 28025
- 2917 Thornbury Corporate Drive, Ste 605, Charlotte, NC 28277
Business card can be horizontal or vertical in Design.
I need to be able to edit it to update and add new employees

Requirements
Must have
• Front:
• - Logo
• - Name & Title (able to be edited)
• - phone (704-555-0186) & Email (need to be able to edit)
• - Address: 5263 Walnut Hollow Pkwy, Ste 412
• Concord, NC 28027
• Back:
• Appointment Card design:
• - Name, time, Date
• - 3 locations w/ a check box so the patient knows where to go:
• Dale Fenwick Orthodontics
• - 6735 Orchard Street, Ste 514, Harrisburg, NC 28075
• - 3647 Ridgeway Drive NE, Ste 810, Concord, NC 28025
• - 2917 Thornbury Corporate Drive, Ste 605, Charlotte, NC 28277

```html
<!DOCTYPE html>
<html lang="en">
<head>
<meta charset="UTF-8">
<title>Brightarc Orthodontics – Business &amp; Appointment Card</title>
<link rel="stylesheet" href="https://fonts.googleapis.com/css2?family=Lato:wght@400;700;900&family=Oswald:wght@600&display=swap">
<style>
  :root {
    --bg: #2a2b2d;
    --card-front: #c4c4c4;
    --card-back: #ffffff;
    --brand-blue: #1f6fc0;
    --ink: #1c1c1c;
    --ink-soft: #2e2e2e;
  }
  * { box-sizing: border-box; margin: 0; padding: 0; }
  html, body {
    width: 1200px; height: 1200px; overflow: hidden;
    background: var(--bg);
    font-family: "Lato", sans-serif;
    color: var(--ink);
  }
  .canvas { position: relative; width: 1200px; height: 1200px; }

  .card {
    position: absolute;
    width: 700px; height: 400px;
    box-shadow: 0 18px 40px rgba(0,0,0,.45);
  }
  .card--front { left: 90px; top: 150px; background: var(--card-front); }
  .card--back  { left: 410px; top: 640px; background: var(--card-back); }

  .brand {
    position: absolute; right: 60px; top: 58px;
    display: flex; align-items: center; gap: 12px;
    font-family: "Lato", sans-serif; font-weight: 900;
    font-size: 34px; color: var(--brand-blue); letter-spacing: .2px;
  }
  .brand__dot { width: 16px; height: 16px; border-radius: 50%; background: var(--brand-blue); }

  .rule { position: absolute; height: 2px; background: var(--brand-blue); }

  /* front */
  .card--front .rule--main { left: 220px; right: 60px; top: 140px; }
  .office-address {
    position: absolute; right: 60px; top: 158px;
    text-align: right; font-size: 15px; line-height: 1.35; color: var(--ink-soft);
  }
  .staff { position: absolute; left: 50px; bottom: 40px; width: 300px; }
  .staff__name {
    font-family: "Oswald", sans-serif; font-weight: 600;
    font-size: 28px; text-transform: uppercase; line-height: 1.05; color: var(--ink);
  }
  .staff__title { font-size: 17px; color: var(--brand-blue); margin-bottom: 6px; }
  .staff__rule { height: 2px; background: var(--brand-blue); width: 250px; margin-bottom: 8px; }
  .contact { list-style: none; font-size: 15px; line-height: 1.4; color: var(--ink-soft); }
  .contact li { display: flex; align-items: center; gap: 8px; }
  .contact svg { width: 13px; height: 13px; fill: var(--brand-blue); flex: none; }

  /* back */
  .card--back .rule--top1 { left: 330px; right: 60px; top: 128px; }
  .card--back .rule--top2 { left: 400px; right: 40px; top: 150px; }
  .appt { position: absolute; left: 50px; top: 180px; right: 40px; }
  .appt__row { display: flex; align-items: flex-end; gap: 10px; margin-bottom: 14px; font-weight: 700; font-size: 19px; }
  .appt__line { flex: 1; height: 2px; background: var(--brand-blue); margin-bottom: 5px; }
  .appt__row--date { margin-left: 330px; }
  .practice { font-weight: 900; font-size: 20px; margin: 4px 0 8px 40px; }
  .locations { list-style: none; font-size: 18px; line-height: 1.45; }
  .locations li { display: flex; align-items: center; gap: 16px; }
  .check { width: 18px; height: 18px; border: 2px solid var(--brand-blue); flex: none; }
  .check--marked { background: var(--ink); border-color: var(--ink); }
</style>
</head>
<body>
<main class="canvas">

  <section class="card card--front" aria-label="Business card front">
    <div class="brand"><span class="brand__dot"></span>Brightarc Orthodontics</div>
    <div class="rule rule--main"></div>
    <address class="office-address">5263 Walnut Hollow Pkwy<br>Ste 412 - Concord, NC 28027</address>

    <div class="staff">
      <h1 class="staff__name">Marcus Hale</h1>
      <p class="staff__title">CEO / Manager</p>
      <div class="staff__rule"></div>
      <ul class="contact">
        <li><svg viewBox="0 0 24 24"><path d="M6.6 10.8a15.1 15.1 0 0 0 6.6 6.6l2.2-2.2c.3-.3.7-.4 1-.2 1.1.4 2.3.6 3.6.6.6 0 1 .4 1 1V20c0 .6-.4 1-1 1A17 17 0 0 1 3 4c0-.6.4-1 1-1h3.5c.6 0 1 .4 1 1 0 1.3.2 2.5.6 3.6.1.3 0 .7-.2 1z"/></svg>+704-555-0186</li>
        <li><svg viewBox="0 0 24 24"><path d="M12 2a10 10 0 1 0 0 20 10 10 0 0 0 0-20zm0 2c1 0 2.3 2 2.8 5H9.2C9.7 6 11 4 12 4zM4.3 13a8 8 0 0 1 0-2h2.9a18 18 0 0 0 0 2zm.8 2h2.4c.3 1.4.8 2.7 1.4 3.6A8 8 0 0 1 5.1 15zm4.1 0h5.6c-.5 3-1.8 5-2.8 5s-2.3-2-2.8-5zm0-4h5.6a16 16 0 0 1 0 2H9.2a16 16 0 0 1 0-2zm7.6 2a18 18 0 0 0 0-2h2.9a8 8 0 0 1 0 2zm-.3 2h2.4a8 8 0 0 1-3.8 3.6c.6-.9 1.1-2.2 1.4-3.6z"/></svg>www.brightarcortho.com</li>
        <li><svg viewBox="0 0 24 24"><path d="M2 5h20v14H2zm2 2v.4l8 5.2 8-5.2V7zm0 2.8V17h16V9.8l-8 5.2z"/></svg>hello@brightarcortho.com</li>
      </ul>
    </div>
  </section>

  <section class="card card--back" aria-label="Appointment card back">
    <div class="brand"><span class="brand__dot"></span>Brightarc Orthodontics</div>
    <div class="rule rule--top1"></div>
    <div class="rule rule--top2"></div>

    <div class="appt">
      <div class="appt__row appt__row--date"><span>Date :</span><span class="appt__line"></span></div>
      <div class="appt__row"><span>Name :</span><span class="appt__line"></span></div>
      <div class="appt__row"><span>Time :</span><span class="appt__line"></span></div>
      <p class="practice">Dale Fenwick Orthodontics</p>
      <ul class="locations">
        <li><span class="check check--marked"></span>6735 Orchard Street, Ste 514, Harrisburg, NC 28075</li>
        <li><span class="check"></span>3647 Ridgeway Drive NE, Ste 810, Concord, NC 28025</li>
        <li><span class="check"></span>2917 Thornbury Corporate Drive, Ste 605, Charlotte, NC 28277</li>
      </ul>
    </div>
  </section>

</main>
</body>
</html>
```